Advertisement flyer for fire sprinkler repair parts. The projected audience are contractors.

I need a flyer advertising specific parts that we are stocking at our company "Coastal Valveline Supply." I have attached a picture of our logo. I want the title to say "Fire Pump Repair Parts and Accessories." I want to specifically advertise the following parts: Repack Kits and Repair Parts, Jockey Pumps, Pump Controllers, Casing Relief Valves, Air Release Valves, Suction/Discharge Gauges, Pump Shaft Couplers & Shim Kits, Fire Pump Relief Valves, and UL Listed Pressure Reducing Valves. I have attached pictures of the manufacturers I want to advertise on this flyer. I have also attached pictures of some of the parts we are stocking that I would like to be included somewhere in the flyer. I would like all of the pictures to have a transparent background. Also I would like our phone number :(800)-318-4027, and our website www.valvelinesupply-demo.com included. I made my own design that I have Attached. You do not have to go based off this design, but I would like the basic content to be the same. We do have Same- Day shipping as well as Free Tech Support if you can include that anywhere.

```html
<!DOCTYPE html>
<html lang="en">
<head>
<meta charset="utf-8">
<title>Fire Pump Repair Parts and Accessories – Coastal Valveline Supply</title>
<link href="https://fonts.googleapis.com/css2?family=Open+Sans:wght@700;800&family=Rubik:wght@400;500&display=swap" rel="stylesheet">
<style>
  :root{
    --pink:#d9245f;
    --purple:#8a55a4;
    --navy:#3a4f9f;
    --ink:#2b3566;
    --bullet:#e2214f;
    --paper:#ffffff;
    --stage:#ffffff;
    --rule:#c9ccd6;
  }
  html,body{margin:0;padding:0;width:1200px;height:1200px;overflow:hidden;background:var(--stage);}
  .flyer{
    position:absolute;left:176px;top:0;width:836px;height:1184px;
    transform:scale(1.0135);transform-origin:0 0;
    background:var(--paper);overflow:hidden;
    font-family:"Rubik",sans-serif;color:var(--ink);
  }
  .flyer__art{position:absolute;left:0;top:0;width:836px;height:1184px;}
  .title{
    position:absolute;left:0;width:836px;text-align:center;margin:0;
    font-family:"Open Sans",sans-serif;font-weight:800;color:#fff;letter-spacing:-0.5px;
  }
  .title__main{top:44px;font-size:66px;line-height:80px;}
  .title__sub{top:110px;font-size:50px;line-height:60px;}
  .parts{position:absolute;left:44px;top:632px;margin:0;padding:0;list-style:none;}
  .parts li{position:relative;padding-left:26px;height:31px;font-size:16px;font-weight:500;line-height:26px;}
  .parts li::before{content:"";position:absolute;left:0;top:10px;width:8px;height:8px;border-radius:50%;background:var(--bullet);}
  .divider{position:absolute;left:44px;top:944px;width:748px;height:1px;background:var(--rule);}
  .brand{
    position:absolute;width:190px;text-align:center;font-size:15px;font-weight:500;color:var(--navy);
  }
  .client{position:absolute;left:0;top:1068px;width:836px;display:flex;justify-content:center;align-items:center;gap:12px;}
  .client__mark{width:22px;height:22px;background:var(--pink);}
  .client__name{font-size:34px;font-weight:400;color:var(--navy);}
  .footer__call{position:absolute;left:44px;top:1144px;font-size:16px;font-weight:500;color:#fff;display:flex;align-items:center;gap:6px;}
  .footer__web{position:absolute;left:440px;top:1140px;font-size:15px;font-weight:500;color:#fff;letter-spacing:2px;}
</style>
</head>
<body>
<main class="flyer">
  <svg class="flyer__art" viewBox="0 0 836 1184" aria-hidden="false">
    <defs>
      <linearGradient id="headerGrad" x1="0" y1="0" x2="1" y2="0">
        <stop offset="0" stop-color="#d8245e"/>
        <stop offset="0.5" stop-color="#8d57a6"/>
        <stop offset="1" stop-color="#d8245e"/>
      </linearGradient>
      <linearGradient id="photoGrad" x1="0" y1="0" x2="1" y2="1">
        <stop offset="0" stop-color="#c7463a"/>
        <stop offset="0.45" stop-color="#f2c46e"/>
        <stop offset="1" stop-color="#b8382d"/>
      </linearGradient>
    </defs>
    <rect class="photo" x="0" y="170" width="836" height="460" fill="url(#photoGrad)" role="img" aria-label="Photo of a fire pump room with red piping, blue valves and red electric pumps"/>
    <path class="band-blue" d="M0 172 C250 240 560 240 836 160 L836 175 C560 250 250 260 0 230 Z" fill="var(--navy)"/>
    <path class="header" d="M0 0 H836 V155 C560 240 250 235 0 170 Z" fill="url(#headerGrad)"/>
    <path class="header-edge" d="M0 170 C250 235 560 240 836 155 L836 162 C560 246 250 242 0 178 Z" fill="#fff"/>
    <line x1="97" y1="44" x2="739" y2="44" stroke="#fff" stroke-width="1.5"/>
    <line x1="97" y1="49" x2="739" y2="49" stroke="#fff" stroke-width="1"/>
    <line x1="97" y1="166" x2="739" y2="166" stroke="#fff" stroke-width="1.5"/>
    <line x1="97" y1="171" x2="739" y2="171" stroke="#fff" stroke-width="1"/>
    <path class="wave" d="M0 640 L0 612 C280 560 560 560 836 620 L836 640 Z" fill="#fff"/>
    <path class="wave-blue" d="M0 630 L0 608 C280 555 560 555 836 612 L836 626 C560 575 280 578 0 630 Z" fill="var(--navy)"/>
    <rect x="330" y="595" width="190" height="105" rx="6" fill="#2f49b8" role="img" aria-label="Blue packing tool box"/>
    <rect x="345" y="705" width="175" height="90" rx="6" fill="#c9ccd3" role="img" aria-label="Packing tools and extractor hooks"/>
    <rect x="612" y="625" width="60" height="140" rx="6" fill="#b08a4c" role="img" aria-label="Brass pressure relief valve"/>
    <rect x="705" y="670" width="72" height="250" rx="8" fill="#8fa6c8" role="img" aria-label="Vertical jockey pump"/>
    <rect x="400" y="805" width="210" height="125" rx="8" fill="#a48c78" role="img" aria-label="Pump casing gasket and shaft couplers"/>
    <rect x="0" y="1132" width="836" height="52" fill="var(--navy)"/>
    <path d="M355 1132 H836 V1168 H375 Z" fill="var(--pink)"/>
  </svg>

  <h1 class="title title__main">FIRE PUMP REPAIR</h1>
  <h2 class="title title__sub">PARTS AND ACCESSORIES</h2>

  <ul class="parts">
    <li>Fire Pump Repack Kits</li>
    <li>Jockey Pumps</li>
    <li>Pump Controllers</li>
    <li>Casing Relief Valves</li>
    <li>Air Release Valves</li>
    <li>Suction / Discharge Gauges</li>
    <li>Packing Tools</li>
    <li>Pump Shaft Couplers &amp; Shim Kits</li>
    <li>Fire Pump Relief Valves</li>
    <li>UL Listed Pressure Reducing Valves</li>
  </ul>

  <div class="divider"></div>

  <div class="brand" style="left:30px;top:968px">Halvern Flow</div>
  <div class="brand" style="left:224px;top:968px">Brantley Marsh</div>
  <div class="brand" style="left:414px;top:968px">Steadfast Pump</div>
  <div class="brand" style="left:610px;top:968px">Kestrel Pumps</div>
  <div class="brand" style="left:30px;top:1028px">Dura-Valve</div>
  <div class="brand" style="left:224px;top:1028px">Ardent Fire Pump</div>
  <div class="brand" style="left:414px;top:1028px">TRX Pumps</div>
  <div class="brand" style="left:610px;top:1028px">Pelham Works</div>

  <div class="client">
    <span class="client__mark"></span>
    <span class="client__name">Coastal Valveline Supply</span>
  </div>

  <div class="footer__call">Call Us Today !
    <svg width="14" height="14" viewBox="0 0 24 24" aria-hidden="true"><path fill="#fff" d="M6.6 10.8a15.1 15.1 0 0 0 6.6 6.6l2.2-2.2a1 1 0 0 1 1-.25 11.4 11.4 0 0 0 3.6.57 1 1 0 0 1 1 1V20a1 1 0 0 1-1 1A17 17 0 0 1 3 4a1 1 0 0 1 1-1h3.5a1 1 0 0 1 1 1c0 1.25.2 2.45.57 3.57a1 1 0 0 1-.25 1z"/></svg>
    (800)-318-4027</div>
  <div class="footer__web">www.valvelinesupply-demo.com</div>
</main>
</body>
</html>
```